Stationary design for boutique production house

We need a stationary design for our production house, 'Lorno Productions' based in Singapore. We produce microfilms as well as podcasts, talkshows and events. Our logo is a stylized icon of our director, who is also the executive producer and host of our programs, Lorno. Our main company colors are Red, Black and white. We would like a clean, minimalist design incorporating our existing company logo that conveys a sense of urbanism and elegance.

Logo and font files are attached. f

Target Market(s)

We focus on lifestyle media rather than entertainment.

Industry/Entity Type

Boutique

Font styles to use
Serif
Sans Serif

Colors
ec1f27
ffffff
000000

Requirements
Must have
• Our company logo and at least one of our company colors.
Nice to have
• Our address and contact information.
Should not have
• Changes made to the company logo (using only certain parts of it is fine though)

```html
<!DOCTYPE html>
<html lang="en">
<head>
<meta charset="utf-8">
<title>Lorno Productions – Business Card</title>
<link href="https://fonts.googleapis.com/css2?family=Jost:wght@400;500&display=swap" rel="stylesheet">
<style>
  :root {
    --red: #d0181f;
    --black: #1e1a1a;
    --white: #ffffff;
    --paper: #f7f7f7;
    --ink: #3a3a3a;
    --rule: #d6d6d6;
    --backdrop: #4b4b4b;
  }
  * { margin: 0; padding: 0; box-sizing: border-box; }
  html, body {
    width: 1200px; height: 750px; overflow: hidden;
    background: var(--backdrop);
    font-family: "Jost", sans-serif;
  }
  .stage { position: relative; width: 1200px; height: 750px; }

  .card {
    position: absolute; top: 228px;
    width: 462px; height: 263px; overflow: hidden;
  }

  /* Front */
  .card--front { left: 124px; background: var(--paper); }
  .brand {
    position: absolute; left: 30px; top: 0; width: 170px; height: 252px;
    display: flex; flex-direction: column; align-items: center; justify-content: center; gap: 10px;
  }
  .brand__dot { width: 16px; height: 16px; border-radius: 50%; background: var(--red); }
  .brand__name {
    font-weight: 500; font-size: 19px; line-height: 1.15; text-align: center;
    color: var(--black); letter-spacing: 0.5px;
  }
  .divider {
    position: absolute; left: 227px; top: 44px; width: 1px; height: 172px;
    background: var(--rule);
  }
  .details { position: absolute; left: 261px; top: 44px; color: var(--ink); }
  .details__name {
    font-size: 18px; color: var(--red); line-height: 1.1; letter-spacing: 0.2px;
  }
  .details__role { font-size: 14px; color: var(--black); line-height: 1.2; }
  .details__address { margin-top: 12px; font-size: 12px; line-height: 14px; }
  .contact { list-style: none; margin-top: 10px; }
  .contact li {
    display: flex; align-items: center; gap: 8px;
    font-size: 11.5px; height: 17.6px;
  }
  .contact svg { width: 12px; height: 12px; fill: var(--red); flex: none; }
  .band {
    position: absolute; left: 0; bottom: 0; width: 100%; height: 11px;
    background: var(--red);
  }
  .band__end {
    position: absolute; right: 0; top: 0; width: 46px; height: 100%; background: var(--black);
  }
  .band__mark {
    position: absolute; left: 420px; top: 3px; width: 6px; height: 6px;
    border-radius: 50%; background: var(--white);
  }

  /* Back */
  .card--back { left: 595px; background: var(--red); color: var(--white); }
  .back__brand {
    position: absolute; left: 0; top: 78px; width: 100%;
    display: flex; flex-direction: column; align-items: center; gap: 12px;
  }
  .back__dot { width: 14px; height: 14px; border-radius: 50%; background: var(--white); }
  .back__name { font-weight: 500; font-size: 26px; letter-spacing: 1px; text-align: center; line-height: 1.1; }
  .back__url {
    position: absolute; left: 0; top: 222px; width: 100%; text-align: center;
    font-size: 11px; letter-spacing: 7px;
  }
</style>
</head>
<body>
<main class="stage">
  <section class="card card--front">
    <div class="brand">
      <span class="brand__dot"></span>
      <p class="brand__name">LORNO<br>PRODUCTIONS</p>
    </div>
    <div class="divider"></div>
    <div class="details">
      <h1 class="details__name">DANIEL TAN</h1>
      <p class="details__role">CEO/FOUNDER</p>
      <p class="details__address">18 Lantern Quay Road<br>Singapore 048721</p>
      <ul class="contact">
        <li><svg viewBox="0 0 24 24"><path d="M6.6 10.8a15 15 0 0 0 6.6 6.6l2.2-2.2a1 1 0 0 1 1-.25 11.4 11.4 0 0 0 3.6.57 1 1 0 0 1 1 1V20a1 1 0 0 1-1 1A17 17 0 0 1 3 4a1 1 0 0 1 1-1h3.5a1 1 0 0 1 1 1c0 1.25.2 2.45.57 3.57a1 1 0 0 1-.25 1z"/></svg>6512 3087</li>
        <li><svg viewBox="0 0 24 24"><path d="M7 1h10a2 2 0 0 1 2 2v18a2 2 0 0 1-2 2H7a2 2 0 0 1-2-2V3a2 2 0 0 1 2-2zm0 3v14h10V4z"/></svg>9284 7761</li>
        <li><svg viewBox="0 0 24 24"><path d="M6 2h12v6H6zM3 9h18a1 1 0 0 1 1 1v8h-4v4H6v-4H2v-8a1 1 0 0 1 1-1zm5 7v4h8v-4z"/></svg>6512 3090</li>
        <li><svg viewBox="0 0 24 24"><path d="M2 5h20v14H2zm2 2v.5l8 5 8-5V7z"/></svg>hello@lornoprod.com</li>
        <li><svg viewBox="0 0 24 24"><path d="M12 2a10 10 0 1 0 0 20 10 10 0 0 0 0-20zm-1 17.9A8 8 0 0 1 4.2 10L9 15v1a2 2 0 0 0 2 2zm6.9-2.5A2 2 0 0 0 16 16h-1v-3a1 1 0 0 0-1-1H8v-2h2a1 1 0 0 0 1-1V7h2a2 2 0 0 0 2-2v-.4a8 8 0 0 1 2.9 12.8z"/></svg>www.lornoprod.com</li>
      </ul>
    </div>
    <div class="band">
      <div class="band__end"></div>
      <span class="band__mark"></span>
    </div>
  </section>

  <section class="card card--back">
    <div class="back__brand">
      <span class="back__dot"></span>
      <p class="back__name">LORNO<br>PRODUCTIONS</p>
    </div>
    <p class="back__url">www.lornoprod.com</p>
  </section>
</main>
</body>
</html>
```